The Linen Loft Co

We need a business card design for our wardrobe company.
Please visit our website www.gentlelinenlofts.com to get an idea of who we are.

```html
<!DOCTYPE html>
<html lang="en">
<head>
<meta charset="utf-8">
<title>The Linen Loft Co – Business Card</title>
<link href="https://fonts.googleapis.com/css2?family=Poppins:wght@400;500;600&display=swap" rel="stylesheet">
<style>
  :root {
    --backdrop: #e4e4e4;
    --card: #ffffff;
    --ink: #111111;
    --muted: #a6a6a6;
    --body: #4a4a4a;
  }
  * { margin: 0; padding: 0; box-sizing: border-box; }
  html, body {
    width: 1200px;
    height: 989px;
    overflow: hidden;
    background: var(--backdrop);
    font-family: "Poppins", sans-serif;
  }
  .card {
    position: absolute;
    left: 164px;
    top: 228px;
    width: 884px;
    height: 510px;
    background: var(--card);
    box-shadow: 0 2px 8px rgba(0,0,0,0.12);
  }
  .card__edge {
    position: absolute;
    left: 0; top: 0;
    width: 19px; height: 100%;
    background: var(--ink);
  }
  .brand__mark {
    position: absolute;
    left: 72px;
    top: 73px;
    width: 44px; height: 44px;
    background: var(--ink);
  }
  .brand__name {
    position: absolute;
    left: 223px;
    top: 65px;
    font-size: 21px;
    line-height: 28px;
    font-weight: 500;
    color: var(--ink);
    white-space: nowrap;
  }
  .brand__tagline {
    position: absolute;
    left: 246px;
    top: 99px;
    font-size: 17px;
    line-height: 24px;
    font-weight: 600;
    color: var(--ink);
    white-space: nowrap;
  }
  .person__name {
    position: absolute;
    left: 66px;
    top: 226px;
    font-size: 33px;
    line-height: 40px;
    font-weight: 500;
    color: var(--ink);
    letter-spacing: 0.5px;
    white-space: nowrap;
  }
  .person__role {
    position: absolute;
    left: 66px;
    top: 263px;
    font-size: 22px;
    line-height: 26px;
    font-weight: 500;
    color: var(--muted);
  }
  .address {
    position: absolute;
    left: 66px;
    top: 308px;
    font-size: 21px;
    line-height: 27px;
    color: var(--body);
    font-style: normal;
    white-space: nowrap;
  }
  .contacts {
    position: absolute;
    left: 68px;
    top: 372px;
    list-style: none;
  }
  .contacts li {
    display: flex;
    align-items: center;
    gap: 9px;
    height: 27.5px;
    font-size: 21px;
    color: var(--body);
    white-space: nowrap;
  }
  .contacts svg {
    width: 19px; height: 19px;
    fill: var(--ink);
    flex: none;
  }
</style>
</head>
<body>
  <section class="card">
    <div class="card__edge"></div>

    <div class="brand__mark"></div>
    <div class="brand__name">THE LINEN LOFT CO</div>
    <div class="brand__tagline">Crafted to Fit Your Space</div>

    <div class="person__name">DANIEL HARPER</div>
    <div class="person__role">President</div>

    <address class="address">
      Orchard House, 42 Mill Lane,<br>
      London N1 7QT
    </address>

    <ul class="contacts">
      <li>
        <svg viewBox="0 0 24 24"><path d="M6.6 10.8a15.1 15.1 0 0 0 6.6 6.6l2.2-2.2a1 1 0 0 1 1-.25 11.4 11.4 0 0 0 3.6.57 1 1 0 0 1 1 1V20a1 1 0 0 1-1 1A17 17 0 0 1 3 4a1 1 0 0 1 1-1h3.5a1 1 0 0 1 1 1c0 1.25.2 2.45.57 3.57a1 1 0 0 1-.25 1z"/></svg>
        020 7946 0815
      </li>
      <li>
        <svg viewBox="0 0 24 24"><path d="M2 5h20v14H2z M3.5 6.5v.6l8.5 6 8.5-6v-.6z M3.5 8.9v8.6h17V8.9l-8.5 6z" fill-rule="evenodd"/></svg>
        info@gentlelinenlofts.com
      </li>
      <li>
        <svg viewBox="0 0 24 24"><path d="M12 2a10 10 0 1 0 0 20 10 10 0 0 0 0-20zm-1 17.9A8 8 0 0 1 4.2 10.2L9 15v1a2 2 0 0 0 2 2zm6.9-2.5A2 2 0 0 0 16 16h-1v-3a1 1 0 0 0-1-1H8v-2h2a1 1 0 0 0 1-1V7h2a2 2 0 0 0 2-2v-.4a8 8 0 0 1 2.9 12.8z"/></svg>
        www.gentlelinenlofts.com
      </li>
    </ul>
  </section>
</body>
</html>
```